Design Website to Recruit next Generation of Steel Harbor's Order Vantage

Design a cool website that provides just enough information to be intriguing to teenagers who compete in combat sports. The format is to make this an invite-only team of high-school-aged competitors in combat sports (predominately Jiu Jitsu right now). Cinder Ravens can participate in similar assignments to earn consideration. We are modeled after the Order Vantage formed in Steel Harbor and would like to keep that look and feel. The document attached "OV - Ideas and Content for Website" shows our initial thoughts and here is more about us:

Goal - To promote the success of committed teenage Jiu Jitsu competitors who excel through focused preparation and deliberate practice.

Why - Prove the core principles of success.

How - Success is its own reward and always entails an element of the unknown/uncontrollable. We reward preparation. Setting clear goals (SMART), deliberate practice, building mental models (domain specific knowledge), restorative recovery, nutritional coaching, power of teaching others, sports science (strength & conditioning), expert guidance, personalized development plans, accountability, Quantified Self, gamification and competitive challenges. What - We will win at the highest of levels across the fight world by applying the general principles of success. These lessons will be carried with them to other areas of their lives.

Our primary goal with the website would be to share our company’s mission statement and promote the success of our sponsored athletes.

The only social media account we have currently is Pixtrelle's @ordervantageK7 (recently established). If you want more of an idea for what our online presence should feel like, then I would suggest watching these two scenes from Steel Harbor:

Recruiting: This scene shows the process for joining Order Vantage: https://vidrelo.net/Qk82LmTrA

Order Vantage Assignments: This shows how assignments are handed out for members to accomplish: https://vidrelo.net/Zp41XwNeB

Order Vantage Color Assignment: This is their first large assignment and where the green color comes from: https://vidrelo.net/Hd67VcJuC

It is also worth noting that "less is more" considering the first rule is, "you do not talk about..." That should carry over to our website and social media presence. We want to share just enough to be intriguing to inquiring minds and motivational for members, but no more.

I have uploaded a bunch of content, but just wanted to give you a broader idea. Feel free to design as you see fit...
Updates

Please stay tuned for the "burning smiley face" files. I have purchased a rendering of it so we have a proprietary vector image to use on our site. There will also be files for different versions of the Order Vantage//OV logos for various subcategories. Here is how they are to be applied: Circled = Primary (for main/landing page), Jiu Jitsu = Pyramid, Wrestling = Traditional, Muay Thai = Rolled, and Legacy OV = Original (coming soon).

Target Market(s)

Teenage competitors of combat sports, their parents, and sponsors of those athletes

Industry/Entity Type

Martial Arts & High School Sports

Coding

Coded - Design and coding required

Number of Pages Required

5+ page

Font styles to use
Sans Serif
Other font styles liked:
• See font in "Circled Logo"

Colors
59FF00
82FF00
B8FF75
E3FFCB
F4FFEA
EB3D1F
EC4F4E
F09395
F8D3D4
FCEDEE

Requirements
Must have
• Cool landing page with logo and brief summary of what we do. Page with 8 rules and explanation for earning an invitation. Plus, accomplishments page for memorializing the success of sponsored "Cinder Ravens"
Should not have
• Individual names

```html
<!DOCTYPE html>
<html lang="en">
<head>
<meta charset="utf-8">
<title>Order Vantage</title>
<link rel="stylesheet" href="https://fonts.googleapis.com/css2?family=Alegreya:ital,wght@1,700;1,800&family=Poppins:wght@400;500&display=swap">
<style>
:root{
  --red:#e33b4c;
  --red-dark:#c92f3f;
  --ink:#111111;
  --text:#222222;
  --white:#ffffff;
  --black:#000000;
  --head:"Alegreya", Georgia, serif;
  --body:"Poppins", Arial, sans-serif;
}
*{margin:0;padding:0;box-sizing:border-box}
html,body{width:1200px;height:5115px;overflow:hidden}
body{position:relative;background:var(--white);font-family:var(--body);color:var(--text)}
.abs{position:absolute}
.head{font-family:var(--head);font-style:italic;font-weight:700}
.btn{position:absolute;background:var(--red);color:var(--white);font-family:var(--head);font-style:italic;font-weight:700;font-size:20px;border-radius:8px;padding:6px 16px;line-height:1.2}

/* hero */
.hero{left:0;top:0;width:1200px;height:716px;background:radial-gradient(ellipse at 70% 60%,#4a4a4a 0%,#262626 40%,#0b0b0b 100%)}
.logo{left:112px;top:30px;font-size:40px;color:var(--red)}
.nav{top:42px;right:182px;display:flex;gap:24px;font-size:15px;color:var(--white)}
.hero-title{left:0;width:1200px;top:226px;text-align:center;font-size:62px;color:var(--white)}
.hero-sub{left:0;width:1200px;top:328px;text-align:center;font-size:32px;line-height:47px;color:var(--white);font-weight:400}
.hero .btn{left:530px;top:514px}
.dots{left:548px;top:656px;display:flex;gap:10px}
.dots span{width:10px;height:10px;background:var(--white)}

/* about */
.frame-a{left:110px;top:805px;width:188px;height:172px;background:var(--red)}
.frame-b{left:418px;top:1162px;width:152px;height:173px;background:var(--red)}
.portrait{left:130px;top:821px;width:422px;height:496px;background:linear-gradient(160deg,#6a5040,#3a2a22 55%,#a89080)}
.about-title{left:620px;top:796px;width:460px;font-size:38px;line-height:48px;color:var(--red)}
.about-copy{left:620px;top:962px;width:420px;font-size:14.5px;line-height:30px;color:var(--text)}
.about-copy p+p{margin-top:18px}
.about .btn{left:620px;top:1286px}

/* pillars */
.pillars-title{left:0;width:1200px;top:1414px;text-align:center;font-size:38px;line-height:48px;color:var(--red)}
.ring-set{left:0;top:1530px}
.pillar{position:absolute;width:300px;text-align:center}
.pillar h3{font-family:var(--head);font-style:italic;font-weight:700;font-size:38px;color:var(--ink)}
.pillar .icon{width:74px;height:74px;margin:16px auto 20px;border:3px solid var(--red);border-radius:50%;background:#fbe7e9}
.pillar p{font-size:14.5px;line-height:47px;color:var(--text)}

/* rules */
.rules{left:0;top:2550px;width:745px;height:620px;background:var(--red)}
.rules-photo{left:745px;top:2550px;width:455px;height:620px;background:linear-gradient(180deg,#8a8682,#d9d6d0 45%,#2c2a28 60%,#cfcbc4)}
.rules-title{left:112px;top:2570px;font-size:36px;line-height:48px;color:var(--white)}
.rules-list{left:112px;top:2696px;list-style:none;color:var(--white);font-size:14.5px;line-height:47.3px}
.rules-list li{position:relative;padding-left:24px}
.rules-list li::before{content:"";position:absolute;left:0;top:19px;width:10px;height:10px;border-radius:50%;background:var(--white)}
.rules .btn,.btn-light{left:112px;top:3098px;background:var(--white);color:var(--red)}

/* faq */
.faq-title{left:0;width:1200px;top:3244px;text-align:center;font-size:38px;color:var(--red)}
.faq-card{left:225px;top:3352px;width:745px;height:228px;background:var(--white);box-shadow:0 4px 22px rgba(0,0,0,.16)}
.faq-q{position:absolute;left:0;width:100%;text-align:center;font-family:var(--head);font-style:italic;font-weight:700;font-size:40px;color:var(--ink)}
.faq-a{position:absolute;text-align:center;font-size:14.5px;line-height:31px;color:var(--text)}

/* video */
.video{left:0;top:3889px;width:1200px;height:548px;background:radial-gradient(ellipse at 50% 40%,#3c3026,#17120e 60%,#060504)}
.play{left:576px;top:4150px}

/* footer */
.footer{left:0;top:4646px;width:1200px;height:469px;background:var(--black)}
.quote{left:111px;top:4526px;width:978px;height:229px;background:var(--white);box-shadow:0 4px 20px rgba(0,0,0,.12);text-align:center;padding-top:42px;font-size:36px;line-height:47px;color:var(--red)}
.foot-logo{left:0;width:1200px;top:4816px;text-align:center;font-size:42px;color:var(--white)}
.foot-nav{left:0;width:1200px;top:4902px;display:flex;justify-content:center;gap:30px;font-size:15px;color:var(--white)}
.social{left:0;width:1200px;top:4966px;display:flex;justify-content:center;gap:36px}
.social span{width:14px;height:14px;border-radius:50%;background:var(--white)}
.rule-line{left:0;top:5043px;width:1200px;height:1px;background:#555}
.copyright{left:0;width:1200px;top:5072px;text-align:center;font-size:12px;color:var(--white)}
</style>
</head>
<body>

<section class="hero abs" role="img" aria-label="Dark smoky photo of a martial artist in a gi, hands wrapped">
</section>
<div class="logo abs head">Order Vantage</div>
<nav class="nav abs"><span>Home</span><span>About Us</span><span>Pages</span><span>Blog</span><span>Gallery</span><span>Contact</span></nav>
<h1 class="hero-title abs head">Marlo built himself an army.</h1>
<p class="hero-sub abs head" style="font-weight:700">Why was Marlo Veck building an army?<br>To what purpose?<br>For what greater good?</p>
<div class="hero"><span class="btn">Get Started</span></div>
<div class="dots abs"><span></span><span></span><span></span><span></span><span></span></div>

<section class="about">
  <div class="frame-a abs"></div>
  <div class="frame-b abs"></div>
  <div class="portrait abs" role="img" aria-label="Portrait photo of the team's figurehead in tinted glasses"></div>
  <h2 class="about-title abs head">How Much Can You know About Youself if Youve never been in a fight?</h2>
  <div class="about-copy abs">
    <p>To inttoduce and Appiy the core principles of success to highschool aged jia jitsu Compatitors.<br>We strive to work smarter not just harder so they can achive their full Order Vantage</p>
    <p>Lorem ipsum dolor sit amet, consectetur adipiscing elit, sed do eiusmod tempor incididunt ut labore et dolore magna aliqua. Ut enim ad minim veniam, quis nostrud exercitation ullamco laboris nisi ut aliquip ex ea commodo consequat.</p>
  </div>
  <span class="btn">In Marlo We Trust</span>
</section>

<h2 class="pillars-title abs head">Success is its own reward,<br>so we celebrate Preparation.</h2>
<svg class="ring-set abs" width="1200" height="950" viewBox="0 0 1200 950" aria-hidden="true">
  <g fill="none" stroke="#e33b4c" stroke-width="40">
    <circle cx="600" cy="258" r="230"/>
    <circle cx="372" cy="685" r="230"/>
    <circle cx="830" cy="685" r="230"/>
  </g>
</svg>
<div class="pillar" style="left:450px;top:1650px">
  <h3>Spirit</h3>
  <div class="icon" role="img" aria-label="Line icon of joined hands"></div>
  <p>Lorem ipsum dolor<br>Lorem ipsum dolor<br>Lorem ipsum dolor</p>
</div>
<div class="pillar" style="left:222px;top:2050px">
  <h3>Techical/Mind</h3>
  <div class="icon" role="img" aria-label="Line icon of a raised fist"></div>
  <p>Excepteur sint occaecat<br>Excepteur sint occaecat<br>Excepteur sint occaecat</p>
</div>
<div class="pillar" style="left:680px;top:2050px">
  <h3>Body</h3>
  <div class="icon" role="img" aria-label="Line icon of an athlete's body"></div>
  <p>Sed ut perspiciatis<br>Sed ut perspiciatis<br>Sed ut perspiciatis</p>
</div>

<section class="rules abs"></section>
<div class="rules-photo abs" role="img" aria-label="Photo of hands tying a black belt on a white gi"></div>
<h2 class="rules-title abs head">I don't want to die<br>without any scans</h2>
<ul class="rules-list abs">
  <li>Do not talk about ov</li>
  <li>Do not talk about ov</li>
  <li>You protect the reputation of past,present and future</li>
  <li>You do not contest close matches or complain</li>
  <li>You will serve as a bridge between kid &amp; adult BJJ competiton</li>
  <li>You will alway treat competitors with respect</li>
  <li>You Will attend teammate matches and help them whenever possible</li>
  <li>If you are in, then you have to fight</li>
</ul>
<span class="btn btn-light">Read More</span>

<h2 class="faq-title abs head">Common Questions</h2>
<div class="faq-card abs">
  <h3 class="faq-q" style="top:24px">01.Why the "K7"?</h3>
  <p class="faq-a" style="left:90px;width:565px;top:88px">Lorem ipsum dolor sit amet, consectetur adipiscing elit, sed do eiusmod tempor incididunt ut labore et dolore magna aliqua. Ut enim ad minim veniam, quis nostrud exercitation ullamco laboris nisi ut aliquip ex ea commodo consequat.</p>
  <svg class="abs" style="left:678px;top:164px" width="50" height="50" viewBox="0 0 50 50" aria-hidden="true">
    <g stroke="#111" stroke-width="3" stroke-linecap="round"><line x1="16" y1="4" x2="18" y2="12"/><line x1="4" y1="16" x2="12" y2="18"/><line x1="6" y1="28" x2="12" y2="24"/><line x1="28" y1="6" x2="24" y2="12"/></g>
    <path d="M18 18 L44 30 L33 33 L41 44 L36 48 L28 37 L21 44 Z" fill="#111"/>
  </svg>
</div>
<h3 class="faq-q" style="top:3646px">02.How does Someone set Invited?</h3>
<p class="faq-a" style="left:300px;width:600px;top:3716px">Duis aute irure dolor in reprehenderit in voluptate velit esse cillum dolore eu fugiat nulla pariatur. Excepteur sint occaecat cupidatat non proident, sunt in culpa qui officia deserunt mollit anim id est laborum.</p>

<section class="video abs" role="img" aria-label="Dim photo of a crowd gathered in a basement around a fight"></section>
<svg class="play abs" width="82" height="82" viewBox="0 0 82 82" aria-label="Play video" role="img">
  <circle cx="41" cy="41" r="37" fill="none" stroke="#fff" stroke-width="5"/>
  <path d="M33 26 L57 41 L33 56 Z" fill="#fff"/>
</svg>

<footer class="footer abs"></footer>
<div class="quote abs head">Without Pain<br>without Sacrifice,<br>We Would have nothing</div>
<div class="foot-logo abs head">Order Vantage</div>
<nav class="foot-nav abs"><span>Home</span><span>About Us</span><span>Pages</span><span>Blog</span><span>Gallery</span><span>Contact</span></nav>
<div class="social abs" aria-label="Social links"><span></span><span></span><span></span><span></span><span></span></div>
<div class="rule-line abs"></div>
<p class="copyright abs">© Copyright 2023 Order Vantage.All rights reserved.</p>

</body>
</html>
```